Initial website for sport tech startup

We are currently in the R&D phases of our new product. It’s a headband to prevent concussion in the soccer market initially.

We have 2 products, one that’s basic aimed at the youth market and the other more technology driven that’s aimed at the academies and professional market.

Initially the product will launch in the UK

Target Market(s)

Youth soccer players and parents in UK, Soccer Clubs, Federations.

Industry/Entity Type

Sporting Good

Coding

Coded - Design and coding required

Number of Pages Required

5+ page

Requirements
Must have
• Professional style that can be adapted and changed over the coming months.
Nice to have
• Ecommerce ability in the future.

```html
<!DOCTYPE html>
<html lang="en">
<head>
<meta charset="utf-8">
<title>Cranguard – Bringing Safety to the Sports Concussion Debate</title>
<link href="https://fonts.googleapis.com/css2?family=Roboto+Condensed:wght@400;700&family=Open+Sans:wght@400;600&display=swap" rel="stylesheet">
<style>
:root{
  --blue:#29a9e0;
  --blue-deep:#1e96d1;
  --navy:#1f4f7a;
  --ink:#333;
  --muted:#7a7a7a;
  --soft:#a5a5a5;
  --pale:#f3f8fc;
  --slate:#666;
  --dark:#3a3a3a;
  --white:#fff;
}
*{box-sizing:border-box;margin:0;padding:0}
html,body{width:1200px;height:4488px;overflow:hidden}
body{position:relative;background:var(--white);font-family:"Open Sans",sans-serif;color:var(--muted)}
.head{font-family:"Roboto Condensed",sans-serif;font-weight:700}
.photo{position:absolute}

.site-header{position:absolute;left:0;top:0;width:1200px;height:78px;background:var(--white)}
.site-header .nav-band{position:absolute;left:330px;top:0;width:870px;height:78px;background:var(--blue);clip-path:polygon(0 0,100% 0,100% 100%,42px 100%)}
.brand{position:absolute;left:80px;top:14px;font-family:"Roboto Condensed",sans-serif;font-weight:700;font-size:40px;letter-spacing:2px;color:var(--navy);line-height:50px}
.main-nav{position:absolute;top:30px;left:398px;display:flex;font-size:14px;color:var(--white)}
.main-nav span{margin-right:38px}
.main-nav .search{margin-right:0;border-left:1px solid rgba(255,255,255,.7);padding-left:10px;height:16px;display:flex;align-items:center}

.hero{position:absolute;left:0;top:78px;width:1200px;height:565px;background:linear-gradient(180deg,#2c3440 0%,#48505a 35%,#3e5a3a 80%,#2f4a22 100%)}
.hero-title{position:absolute;left:106px;top:158px;font-size:92px;color:var(--white);letter-spacing:3px;line-height:1}
.hero-lead{position:absolute;left:112px;top:258px;width:490px;font-size:15px;line-height:21px;color:var(--white)}
.cta{position:absolute;left:113px;top:322px;width:236px;height:42px;background:var(--blue);clip-path:polygon(0 0,92% 0,100% 100%,8% 100%);color:var(--white);font-size:14px;font-weight:600;text-align:center;line-height:42px}

.band{position:absolute;height:64px;background:var(--blue)}
.band-title{position:absolute;font-family:"Roboto Condensed",sans-serif;font-weight:700;font-size:40px;line-height:64px;color:var(--white)}
.band-title em{font-style:normal;color:#7c7c7c}
.sub{position:absolute;font-family:"Roboto Condensed",sans-serif;font-weight:700;font-size:24px;line-height:29px;color:var(--blue-deep)}
.copy{position:absolute;font-size:14.5px;line-height:25.6px;color:var(--muted);text-align:justify}

.market{position:absolute;left:0;top:1158px;width:1200px;height:518px;background:var(--pale)}
.stat{position:absolute;top:1730px;width:284px;height:204px;background:var(--white);border:1px solid #eee;box-shadow:0 2px 6px rgba(0,0,0,.08);text-align:center}
.stat .ico{position:absolute;left:107px;top:26px;width:70px;height:70px;border-radius:50%;background:var(--blue)}
.stat p{position:absolute;left:0;top:127px;width:100%;font-size:14.5px;line-height:26px;color:#555}

.strategy{position:absolute;left:0;top:2021px;width:1200px;height:693px;background:var(--pale)}
.feature{position:absolute;font-size:14.5px;line-height:26px;color:#333}
.feature svg{position:absolute;left:-56px;top:-6px}

.divider{position:absolute;left:0;top:2714px;width:1200px;height:87px;background:var(--slate)}

.member{position:absolute;top:2998px;width:312px;height:409px;background:var(--white);border:1px solid #eee;box-shadow:0 2px 6px rgba(0,0,0,.06);text-align:center}
.member .avatar{position:absolute;left:109px;top:17px;width:94px;height:94px;border-radius:50%;border:4px solid var(--blue);background:linear-gradient(160deg,#c9d3dc,#8d9aa6)}
.member h3{position:absolute;left:0;top:142px;width:100%;font-family:"Roboto Condensed",sans-serif;font-weight:700;font-size:24px;color:var(--blue-deep)}
.member .role{position:absolute;left:0;top:176px;width:100%;font-family:"Roboto Condensed",sans-serif;font-size:17px;color:#444}
.member .bio{position:absolute;left:36px;top:218px;width:240px;font-size:13px;line-height:25.6px;color:var(--soft);text-align:justify;text-align-last:center}

.advisory{position:absolute;left:0;top:3501px;width:1200px;height:223px;background:linear-gradient(90deg,#2e2e2e,#474747 50%,#2e2e2e)}
.advisory h2{position:absolute;left:0;top:44px;width:100%;text-align:center;font-family:"Roboto Condensed",sans-serif;font-weight:700;font-size:24px;color:var(--white)}
.advisory p{position:absolute;left:140px;top:93px;width:920px;text-align:center;font-size:14.5px;line-height:26px;color:#e6e6e6}

.dist-title{position:absolute;left:0;top:3800px;width:1200px;text-align:center;font-family:"Roboto Condensed",sans-serif;font-weight:700;font-size:24px;color:var(--blue-deep)}
.dist-copy{position:absolute;left:140px;top:3841px;width:920px;text-align:center;font-size:14.5px;line-height:26px;color:var(--muted)}
.partner{position:absolute;top:3944px;height:56px;background:#c8ced4;border-radius:6px}

.site-footer{position:absolute;left:0;top:4094px;width:1200px;height:394px;background:var(--slate);color:var(--white)}
.site-footer .brand-foot{position:absolute;left:0;top:40px;width:100%;text-align:center;font-family:"Roboto Condensed",sans-serif;font-weight:700;font-size:42px;letter-spacing:2px}
.foot-nav{position:absolute;left:0;top:148px;width:100%;display:flex;justify-content:center;gap:40px;font-size:14px}
.social{position:absolute;left:0;top:204px;width:100%;display:flex;justify-content:center;gap:22px}
.social span{width:14px;height:14px;border-radius:50%;background:var(--white)}
.legal{position:absolute;left:0;top:264px;width:100%;display:flex;justify-content:center;gap:18px;font-size:12.5px}
.legal i{display:inline-block;width:1px;height:30px;background:rgba(255,255,255,.7);transform:skewX(-20deg);margin-top:-6px}
.copyright{position:absolute;left:0;top:332px;width:100%;text-align:center;font-size:11px}
</style>
</head>
<body>

<header class="site-header">
  <div class="brand">CRANGUARD</div>
  <div class="nav-band"></div>
  <nav class="main-nav">
    <span>Home</span><span>About</span><span>Our Mission</span><span>Market Today</span><span>Marketing Strategy</span><span>Blog</span><span style="margin-right:10px">Contact</span>
    <span class="search"><svg width="14" height="14" viewBox="0 0 14 14"><circle cx="6" cy="6" r="4.5" fill="none" stroke="#fff" stroke-width="1.6"/><line x1="9.3" y1="9.3" x2="13" y2="13" stroke="#fff" stroke-width="1.6"/></svg></span>
  </nav>
</header>

<section class="hero" role="img" aria-label="Footballer in red kit striking a ball in a floodlit stadium">
  <h1 class="hero-title head">CRANGUARD</h1>
  <p class="hero-lead">Lorem ipsum dolor sit amet consectetur adipiscing elit sed do eiusmod tempor incididunt ut la</p>
  <div class="cta">GET STARTED</div>
</section>

<div class="band" style="left:0;top:711px;width:435px;clip-path:polygon(0 0,86% 0,100% 100%,0 100%)"></div>
<h2 class="band-title" style="left:110px;top:711px">OUR <em>MISSION</em></h2>
<h3 class="sub" style="left:110px;top:790px;width:450px">CRANGUARD – BRINGING SAFETY TO THE SPORTS CONCUSSION DEBATE</h3>
<p class="copy" style="left:111px;top:871px;width:472px">Cranguard is designing and developing head protection products to reduce the likelihood of concussion when playing sports. Exploring and understanding medical insights, material science and composites research, current and former players experiences and governing bodies guidelines has allowed Cranguard to develop the safety, style, form and function requirements of a suitable product to bring to market in Q4 2020.</p>
<div class="photo" role="img" aria-label="Injured player lying on the pitch holding his head" style="left:632px;top:728px;width:457px;height:345px;background:linear-gradient(180deg,#5f9a3c,#4d8a2e)"></div>

<section class="market"></section>
<div class="photo" role="img" aria-label="Players training on an artificial pitch" style="left:96px;top:1245px;width:454px;height:345px;background:linear-gradient(180deg,#e8ecef 0%,#cfd8dc 55%,#5b8a4a 80%,#4a7a3a 100%)"></div>
<div class="band" style="left:571px;top:1228px;width:629px;clip-path:polygon(0 0,100% 0,100% 100%,8% 100%)"></div>
<h2 class="band-title" style="left:627px;top:1228px">THE <em>MARKET TODAY</em></h2>
<h3 class="sub" style="left:629px;top:1300px;width:520px">THERE IS A POTENTIAL £1BN MARKET IN THE UK ALONE</h3>
<p class="copy" style="left:629px;top:1379px;width:493px">Soccer has no head protection product despite recent high profile head injuries, concern over the long term damage of heading the ball and greater damage of concussion in women. There are in excess of 11m people actively playing football in the UK alone (8m men, 3m women). There is no product that exists for netball, field hockey and lacrosse, as further example of the market potential of our product.</p>

<div class="stat" style="left:127px"><div class="ico"><svg width="70" height="70" viewBox="0 0 70 70"><rect x="22" y="24" width="26" height="16" rx="2" fill="none" stroke="#fff" stroke-width="2"/><circle cx="35" cy="32" r="4" fill="none" stroke="#fff" stroke-width="2"/><path d="M20 46h30" stroke="#fff" stroke-width="2"/></svg></div><p>YOUTH SPEND £800PA<br>ON SPORTS KITS</p></div>
<div class="stat" style="left:458px"><div class="ico"><svg width="70" height="70" viewBox="0 0 70 70"><path d="M28 22l-7 5 3 5 4-2v16h14V30l4 2 3-5-7-5h-4a4 4 0 01-6 0z" fill="none" stroke="#fff" stroke-width="2"/></svg></div><p>UK SPORTSWEAR MARKET IS<br>FORECAST TO REACH £6.7BN</p></div>
<div class="stat" style="left:789px"><div class="ico"><svg width="70" height="70" viewBox="0 0 70 70"><rect x="22" y="22" width="22" height="26" rx="2" fill="none" stroke="#fff" stroke-width="2"/><circle cx="44" cy="40" r="6" fill="var(--blue)" stroke="#fff" stroke-width="2"/><path d="M26 29h14M26 35h10" stroke="#fff" stroke-width="2"/></svg></div><p>AV ADULT SPEND £700 PA<br>ON SPORTS KITS</p></div>

<section class="strategy"></section>
<div class="band" style="left:394px;top:2089px;width:806px;clip-path:polygon(0 0,100% 0,100% 100%,5% 100%)"></div>
<h2 class="band-title" style="left:441px;top:2089px">MARKETING <em>STRATEGY</em></h2>
<div class="photo" role="img" aria-label="Footballer in red kit about to strike a ball in a stadium" style="left:111px;top:2155px;width:302px;height:470px;background:linear-gradient(160deg,#3a3f46,#6a4a2e 55%,#2f4a22)"></div>
<h3 class="sub" style="left:441px;top:2166px;width:620px">Engage at all levels, youth, academies, professionals and amateurs</h3>
<p class="copy" style="left:441px;top:2235px;width:648px">With our initial product we will directly engage with the youth football market, through local RFC's (Regional Football Council) to access local clubs, state and independent schools to get the product on their mandatory kit list for sport and through organsations such as the GFA to access the millions of non-league and amateur footballers across the UK. V2 of the product will allow us to target professional clubs effectively with the data analytics solution, also applicable to youth academies, club and independent. In Q2 2021 we will assess the need for distribution partners across Europ 2021 we will assess the need for distribution partners across Europe.</p>

<div class="feature" style="left:498px;top:2451px"><svg width="36" height="36" viewBox="0 0 36 36"><rect x="3" y="5" width="30" height="27" fill="none" stroke="#333" stroke-width="1.5"/><path d="M3 13h30M3 21h30M13 5v27M23 5v27" stroke="#333" stroke-width="1.2"/></svg>R&amp;D FINALISATION</div>
<div class="feature" style="left:852px;top:2451px"><svg width="40" height="38" viewBox="0 0 40 38"><path d="M2 34l14-22 8 12 5-6 9 16z" fill="none" stroke="#333" stroke-width="1.5"/><path d="M22 4v10M22 4l7 3-7 3" fill="none" stroke="#333" stroke-width="1.5"/></svg>PRODUCT CONCEPT TRIALS<br>MFR &amp; COMPOSITES SELECTED</div>
<div class="feature" style="left:498px;top:2535px"><svg width="38" height="38" viewBox="0 0 38 38"><circle cx="17" cy="21" r="14" fill="none" stroke="#333" stroke-width="1.5"/><circle cx="17" cy="21" r="8" fill="none" stroke="#333" stroke-width="1.5"/><circle cx="17" cy="21" r="2.5" fill="#333"/><path d="M17 21L32 6M28 4v6h6" fill="none" stroke="#333" stroke-width="1.5"/></svg>APP DEVELOPMENT<br>UK LAUNCH WITH CLUBS, PLAYERS</div>
<div class="feature" style="left:852px;top:2535px"><svg width="38" height="38" viewBox="0 0 38 38"><path d="M5 5l28 28M33 5L5 33" stroke="#333" stroke-width="3"/><circle cx="7" cy="7" r="4" fill="none" stroke="#333" stroke-width="1.5"/><circle cx="31" cy="7" r="4" fill="none" stroke="#333" stroke-width="1.5"/></svg>CHIP ENABLED PRODUCT TRIALS</div>

<div class="divider"></div>

<div class="band" style="left:0;top:2801px;width:801px;clip-path:polygon(0 0,95% 0,100% 100%,0 100%)"></div>
<h2 class="band-title" style="left:0;top:2801px;width:1200px;text-align:center">OUR <em>TEAM</em></h2>
<h3 class="sub" style="left:0;top:2884px;width:1200px;text-align:center">Successful Entrepreneurs, industry experts and people that deliver.</h3>
<p class="copy" style="left:110px;top:2919px;width:980px;text-align:center">Our team is made of individuals with an enviable record of success across many sectors, delivering for investors and employers every time. In addition to the core team we have an advisory board made up of experts from across sport.</p>

<article class="member" style="left:110px"><div class="avatar" role="img" aria-label="Portrait of Martin Hale"></div><h3>MARTIN HALE</h3><div class="role">Chief Executive Officer</div><p class="bio">From leading edge technology to white label product distribution and most recently sport. Martin has excelled as a leader of start-ups and has worked with sporting clubs and federations across UK &amp; Europe.</p></article>
<article class="member" style="left:444px"><div class="avatar" role="img" aria-label="Portrait of Helen Carver"></div><h3>HELEN CARVER</h3><div class="role">Chief Operating Officer</div><p class="bio">From leading edge technology to white label product distribution and most recently sport. Helen has excelled as a leader of start-ups and has worked with sporting clubs and federations across UK &amp; Europe.</p></article>
<article class="member" style="left:779px"><div class="avatar" role="img" aria-label="Portrait of Graham Lowry"></div><h3>GRAHAM LOWRY</h3><div class="role">Chief Commercial Officer</div><p class="bio">From leading edge technology to white label product distribution and most recently sport. Graham has excelled as a leader of start-ups and has worked with sporting clubs and federations across UK &amp; Europe.</p></article>

<section class="advisory" role="img" aria-label="Dimmed photo of footballers competing for the ball">
  <h2>Advisory Board</h2>
  <p>Our initial advisory board is headed by the former chairman of the Players' Guild and chairman of the Grassroots Footballers Association (3m members), Mr Peter Ashcombe. Peter is working with us to liaise with clubs, former players and federations across UK sport.</p>
</section>

<h2 class="dist-title">Distribution</h2>
<p class="dist-copy">From parents to clubs to federations our model is simple; parents of youth players, parents of amateur players, professional players and clubs, academies and all with the support of federations and unions.</p>
<div class="partner" style="left:112px;width:106px"></div>
<div class="partner" style="left:300px;width:150px"></div>
<div class="partner" style="left:524px;width:52px;border-radius:50%"></div>
<div class="partner" style="left:652px;width:114px"></div>
<div class="partner" style="left:845px;width:48px"></div>
<div class="partner" style="left:976px;width:110px"></div>

<footer class="site-footer">
  <div class="brand-foot">CRANGUARD</div>
  <nav class="foot-nav"><span>Home</span><span>About</span><span>Our Mission</span><span>Market Today</span><span>Marketing Strategy</span><span>Blog</span><span>Contact</span></nav>
  <div class="social"><span></span><span></span><span></span><span></span></div>
  <div class="legal"><span>FAQ's</span><i></i><span>Privacy Policy</span><i></i><span>Terms &amp; Condition</span><i></i><span>Contact Us</span></div>
  <div class="copyright">© Copyright, 2020 Allrights Reserved.</div>
</footer>

</body>
</html>
```